Swing Dance Themed Cleaning Company Website

We need a website designed for a cleaning company based in Portland, Oregon called Foxtrot Lane. We clean homes and commercial buildings, inside and out.

needs to be vintage and like the velvet tambour. Speakeasy 1920s feel.
needs to be classy.

Check out foxtrotlane.com We are not happy with the site currently.

please look at house scout site for more content https://www.housescoutpro.com/rated.FoxtrotLaneCleaning.48217705.html

Check out my videos on my ClipHaven channel Foxtrot Lane

Target Market(s)

middle class and home owner

Industry/Entity Type

Cleaning Service

Number of Pages Required

3 page

Font styles to use
Other font styles liked:
• jazzrag

Colors

Designer to choose colors to be used in the design.

Requirements
Must have
• must be good on pc and mobile

```html
<!DOCTYPE html>
<html lang="en">
<head>
<meta charset="utf-8">
<title>Foxtrot Lane — Services</title>
<link rel="stylesheet" href="https://fonts.googleapis.com/css2?family=Poiret+One&family=Federo&family=Tulpen+One&display=swap">
<style>
  :root {
    --ink: #000000;
    --gold: #e8e51a;
    --white: #ffffff;
    --wall-red: #f0141c;
    --wall-deep: #c80e14;
    --panel: rgba(150, 30, 28, 0.72);
    --concrete: #cfcfcf;
    --brown: #8a6236;
    --dot: rgba(255, 255, 255, 0.85);
  }
  * { box-sizing: border-box; margin: 0; padding: 0; }
  html, body { width: 1200px; height: 853px; overflow: hidden; background: var(--ink); }
  .page { position: relative; width: 1200px; height: 853px; overflow: hidden; font-family: "Poiret One", sans-serif; }

  .site-header { position: absolute; inset: 0 0 auto 0; height: 98px; background: var(--ink); }
  .brand { position: absolute; left: 46px; top: 18px; color: var(--gold); }
  .brand-row { display: flex; align-items: center; gap: 8px; }
  .brand-mark { width: 34px; height: 34px; background: var(--gold); }
  .brand-name { font-family: "Federo", sans-serif; font-size: 20px; line-height: 1; text-transform: uppercase; letter-spacing: 1px; }
  .brand-tagline { font-family: "Federo", sans-serif; font-size: 8px; margin-top: 8px; letter-spacing: 0.4px; }
  .main-nav { position: absolute; top: 28px; left: 0; right: 0; }
  .main-nav a { position: absolute; color: var(--gold); font-size: 22px; text-decoration: none; letter-spacing: 0; white-space: nowrap; }
  .main-nav a.current { border-bottom: 1px solid var(--gold); padding-bottom: 2px; }

  .hero-backdrop { position: absolute; left: 0; top: 98px; width: 1200px; height: 755px;
    background: linear-gradient(180deg, var(--wall-red) 0%, var(--wall-deep) 45%, var(--wall-red) 80%, var(--wall-red) 84%, #e9e9e9 85%, var(--concrete) 100%); }

  .section-title { position: absolute; top: 106px; left: 0; width: 1200px; text-align: center; color: var(--white); font-size: 56px; font-weight: 400; letter-spacing: 10px; }
  .title-rule { position: absolute; top: 136px; }

  .service-card { position: absolute; top: 212px; width: 352px; height: 457px; background: var(--panel); color: var(--white); text-align: center; }
  .service-card h2 { font-family: "Federo", sans-serif; font-weight: 400; font-size: 27px; letter-spacing: 2px; margin-top: 26px; white-space: nowrap; }
  .service-card ul { list-style: none; margin-top: 42px; font-family: "Tulpen One", sans-serif; font-size: 40px; line-height: 43px; white-space: nowrap; }
  .service-card li::before { content: "• "; }

  .slide-dots { position: absolute; left: 55px; top: 808px; display: flex; gap: 6px; }
  .slide-dots span { width: 21px; height: 21px; border-radius: 50%; background: var(--dot); }
  .slide-dots span.active { background: #888; }

  .footer-block { position: absolute; top: 760px; height: 93px; font-family: "Federo", sans-serif; text-transform: uppercase; color: var(--white); font-size: 11px; letter-spacing: 2px; padding: 14px 0 0 22px; line-height: 27px; white-space: nowrap; }
  .footer-block strong { font-weight: 400; font-size: 12px; }
  .about-teaser { left: 419px; width: 392px; background: var(--ink); }
  .quote-teaser { left: 811px; width: 389px; background: var(--brown); padding-left: 17px; font-size: 10.5px; letter-spacing: 1px; }
  .quote-link { position: absolute; right: 8px; top: 10px; color: var(--gold); font-size: 13px; letter-spacing: 4px; text-decoration: none; }
</style>
</head>
<body>
<div class="page">
  <div class="hero-backdrop" role="img" aria-label="Photo of a row of mops leaning against a bright red wall above a concrete ledge"></div>

  <header class="site-header">
    <div class="brand">
      <div class="brand-row"><span class="brand-mark"></span><span class="brand-name">Foxtrot Lane</span></div>
      <div class="brand-tagline">SPOTLESS SPACES IN STYLE, OREGON</div>
    </div>
    <nav class="main-nav">
      <a href="#" style="left:640px">HOME</a>
      <a href="#" style="left:750px">ABOUT US</a>
      <a href="#" class="current" style="left:907px">SERVICES</a>
      <a href="#" style="left:1067px">CONTACT</a>
    </nav>
  </header>

  <h1 class="section-title">SERVICES</h1>
  <svg class="title-rule" style="left:275px" width="162" height="4"><line x1="0" y1="2" x2="162" y2="2" stroke="#f3c9c9" stroke-width="1.5"/></svg>
  <svg class="title-rule" style="left:762px" width="162" height="4"><line x1="0" y1="2" x2="162" y2="2" stroke="#f3c9c9" stroke-width="1.5"/></svg>

  <section class="service-card" style="left:27px">
    <h2>General House Keeping</h2>
    <ul>
      <li>Floor to ceiling dusting</li>
      <li>Cobweb removal</li>
      <li>Kitchen Cleaning</li>
      <li>Bathroom cleaning</li>
      <li>Sweep, mop and vacuum floors</li>
    </ul>
  </section>
  <section class="service-card" style="left:422px">
    <h2>Move Outs &amp; Detail</h2>
    <ul>
      <li>All general house keeping</li>
      <li>Make your house "move in" ready</li>
      <li>Refrigerator and oven cleaning</li>
      <li>Window washing</li>
      <li>Carpet cleaning</li>
    </ul>
  </section>
  <section class="service-card" style="left:818px">
    <h2>Exterior Services</h2>
    <ul>
      <li>Leaf blowing</li>
      <li>Pressure washing</li>
      <li>Window washing</li>
      <li>Exterior house detail</li>
      <li>Gutter cleaning</li>
    </ul>
  </section>

  <div class="slide-dots"><span></span><span></span><span class="active"></span><span></span></div>

  <div class="footer-block about-teaser">
    <strong>Get to know us.</strong><br>
    We provide our years of cleaning<br>
    experience to homes and businesses
  </div>
  <div class="footer-block quote-teaser">
    <strong>Contact us for a quote,</strong><br>
    to book a cleaning, or for any other reason.<br>
    We're looking forward to hearing from you!
    <a href="#" class="quote-link">CLICK HERE</a>
  </div>
</div>
</body>
</html>
```